Card Design for my dog training business Brightpaw Obedience

Need a business card design for my dog training business with my new logo. Want the card to come off professional yet fun. Want it to be very eye catchy as well. I normally have these at vet clinics, pet stores, and groomers. so need it to look better than my competitors.
Target Market(s)
dog owners
Industry/Entity Type
Dog Training
Contact Information for Business Card
needs logo, my name and info
Font styles to use
Serif
Colors
0255a3
ffffff
ec1f27
000000
333333
fbfbfb
Requirements
Must have
- Brightpaw Obedience
- Felix Orland
- 415 903 2276
- info@brightpawobedience.example
- www.brightpawobedience.example

```html
<!DOCTYPE html>
<html lang="en">
<head>
<meta charset="utf-8">
<title>Brightpaw Obedience – Business Card</title>
<link rel="stylesheet" href="https://fonts.googleapis.com/css2?family=Cormorant+Garamond:ital,wght@0,500;1,500&family=Montserrat:wght@400;500&display=swap">
<style>
  :root {
    --brand-blue: #0255a3;
    --brand-blue-soft: #9fbfe2;
    --brand-blue-mist: #dbe7f4;
    --card-black: #1d1e22;
    --ink: #333333;
    --ink-dark: #000000;
    --paper: #fbfbfb;
    --white: #ffffff;
    --stage: #e6e7ea;
    --faint: #e4e4e4;
  }
  * { box-sizing: border-box; margin: 0; padding: 0; }
  html, body { width: 1200px; height: 900px; overflow: hidden; }
  body {
    background: var(--stage);
    position: relative;
    font-family: "Montserrat", sans-serif;
  }
  .card {
    position: absolute;
    left: 250px;
    width: 700px;
    height: 400px;
    overflow: hidden;
    box-shadow: 0 6px 18px rgba(0,0,0,0.18);
  }

  /* Front */
  .card--front { top: 40px; background: var(--card-black); }
  .front__brand {
    position: absolute;
    left: 38px;
    top: 148px;
    width: 170px;
    color: var(--white);
    font-family: "Cormorant Garamond", serif;
    font-weight: 500;
    font-size: 32px;
    line-height: 1.05;
  }
  .front__art {
    position: absolute;
    left: 200px;
    top: 26px;
    width: 470px;
    height: 360px;
    border: 7px solid var(--brand-blue);
    outline: 5px solid var(--white);
    background:
      radial-gradient(ellipse at 35% 45%, var(--white) 0%, var(--white) 22%, rgba(255,255,255,0) 50%),
      radial-gradient(ellipse at 72% 38%, var(--white) 0%, rgba(255,255,255,0) 42%),
      linear-gradient(150deg, var(--brand-blue-mist) 0%, var(--brand-blue-soft) 55%, var(--brand-blue) 100%);
  }

  /* Back */
  .card--back { top: 460px; background: var(--paper); }
  .back__watermark {
    position: absolute;
    right: 0;
    top: 0;
    width: 440px;
    height: 280px;
    background: radial-gradient(ellipse at 55% 50%, var(--faint) 0%, rgba(228,228,228,0.5) 50%, rgba(251,251,251,0) 78%);
  }
  .back__brand {
    position: absolute;
    left: 40px;
    top: 48px;
    display: flex;
    align-items: center;
    gap: 10px;
    font-family: "Cormorant Garamond", serif;
    font-weight: 500;
    font-size: 26px;
    line-height: 1.05;
    color: var(--ink-dark);
  }
  .back__brand-mark { width: 14px; height: 14px; background: var(--ink-dark); flex: none; }
  .back__name {
    position: absolute;
    right: 60px;
    top: 70px;
    font-weight: 500;
    font-size: 22px;
    letter-spacing: 0.04em;
    color: var(--ink-dark);
  }
  .contact {
    position: absolute;
    left: 40px;
    top: 190px;
    list-style: none;
    font-size: 15px;
    color: var(--ink);
  }
  .contact li { display: flex; align-items: center; gap: 12px; height: 28px; }
  .contact svg { width: 16px; height: 16px; fill: var(--brand-blue); flex: none; }
  .tagline {
    position: absolute;
    left: 40px;
    bottom: 42px;
    font-family: "Cormorant Garamond", serif;
    font-style: italic;
    font-weight: 500;
    font-size: 32px;
    color: var(--brand-blue);
  }
</style>
</head>
<body>
  <section class="card card--front" aria-label="Card front">
    <div class="front__brand">Brightpaw<br>Obedience</div>
    <div class="front__art" role="img" aria-label="Blue and white illustration of two dogs inside a regional outline"></div>
  </section>

  <section class="card card--back" aria-label="Card back">
    <div class="back__watermark" role="img" aria-label="Faint large grey dog illustration"></div>
    <div class="back__brand"><span class="back__brand-mark"></span><span>Brightpaw<br>Obedience</span></div>
    <h1 class="back__name">FELIX ORLAND</h1>
    <ul class="contact">
      <li>
        <svg viewBox="0 0 16 16" aria-hidden="true"><path d="M4 1 L6.5 1 L7.5 4.5 L5.7 5.7 C6.6 7.8 8.2 9.4 10.3 10.3 L11.5 8.5 L15 9.5 L15 12 C15 13.7 13.7 15 12 15 C6 15 1 10 1 4 C1 2.3 2.3 1 4 1 Z"/></svg>
        <span>415 903 2276</span>
      </li>
      <li>
        <svg viewBox="0 0 16 16" aria-hidden="true"><path d="M1 3 H15 V13 H1 Z M2 4 L8 9 L14 4 Z" fill-rule="evenodd"/></svg>
        <span>info@brightpawobedience.example</span>
      </li>
      <li>
        <svg viewBox="0 0 16 16" aria-hidden="true"><circle cx="8" cy="8" r="7"/><path d="M1 8 H15 M8 1 C5 4 5 12 8 15 C11 12 11 4 8 1" stroke="#fbfbfb" stroke-width="1" fill="none"/></svg>
        <span>www.brightpawobedience.example</span>
      </li>
    </ul>
    <p class="tagline">“Training dogs across the Bay one dog at a time.”</p>
  </section>
</body>
</html>
```